Stationery Design Project for High End Wealth Management Firm

We need a stationery design for our high-end wealth management firm. Our clientele are affluent and our brand is built around providing investment services with world-class service.

The final concepts should provide a business card, letterhead, and envelope.

We like the idea of having text on the front and back and we MUST have black front and back business cards.
For the business card we have the following that needs to be included:
Company Logo & Tagline
Employee Name
Employee title
Employee Email
Website
2 seperate office cities, addresses, and phone numbers
Financial disclosure (small print)

Having black envelopes would be neat, but black is not a must for the envelopes.
Updates

Project Deadline Extended
Reason: To give the concept one more day of revisions.

Project Deadline Extended
Reason: To allow for more concepts and designs.

Target Market(s)

High Net Worth

Industry/Entity Type

Business

Requirements
Must have
• The following disclosure must be on the back of the card in small print:

Investment Advisory Services offered through Harrowfield Asset Partners LLC, a NFR Registered Investment Advisor. Vantory Wealth Management LLC is not affiliated with Harrowfield Asset Partners LLC.

Black business cards are also a must have.

Please utilize each of the 3 components of our logo in the design.

Please use our white background logo elements when designing our letterhead if you need them.
Nice to have
• Please use our company colors when designing. Utilize a combination of the elements of our logo that we have attached.

We are going to be printing our business cards on letterpress.

```html
<!DOCTYPE html>
<html lang="en">
<head>
<meta charset="utf-8">
<title>Vantory Wealth Management Stationery</title>
<link rel="stylesheet" href="https://fonts.googleapis.com/css2?family=Arimo:wght@400;700&display=swap">
<style>
:root{
  --backdrop:#47474a;
  --card-black:#0c0c0c;
  --paper:#ffffff;
  --gold:#c8893c;
  --bronze:#b8652a;
  --ink:#1e1e1e;
  --soft-ink:#d8d8d8;
  --mark-tint:#f1e6da;
}
*{margin:0;padding:0;box-sizing:border-box}
html,body{width:1200px;height:849px;overflow:hidden}
body{background:var(--backdrop);font-family:"Arimo",Arial,sans-serif;position:relative}
.sheet{position:absolute}

/* letterhead (bottom layer) */
.letterhead{left:563px;top:40px;width:595px;height:768px;background:var(--paper);box-shadow:0 3px 8px rgba(0,0,0,.35);z-index:1;overflow:hidden}
.letterhead .paper-brand{left:192px;top:44px}
.letterhead .paper-tagline{left:192px;top:92px}
.letterhead .hairline.top{left:30px;right:30px;top:124px}
.letterhead .watermark{left:160px;top:250px;width:340px;height:340px}
.letterhead .hairline.bottom{left:40px;right:40px;top:700px}
.letterhead .address{top:712px}

/* business cards */
.card{background:var(--card-black);width:245px;height:142px;top:143px;box-shadow:0 2px 6px rgba(0,0,0,.45);color:var(--soft-ink);z-index:2;overflow:hidden}
.card--front{left:111px}
.card--back{left:395px}
.card .brand{position:absolute;left:0;right:0;top:52px;display:flex;align-items:center;justify-content:center;gap:6px}
.brand-dot{width:14px;height:14px;border-radius:50%;background:var(--gold);flex:none}
.brand-name{font-size:12px;letter-spacing:1px;color:var(--soft-ink);font-weight:400;white-space:nowrap}
.card .brand-name{font-size:8.5px;letter-spacing:.6px}
.card .brand-dot{width:12px;height:12px}
.card .tagline{position:absolute;left:0;right:0;top:80px;text-align:center;font-size:5.2px;color:var(--soft-ink)}
.card .rule{position:absolute;left:26px;right:26px;height:1px;background:linear-gradient(90deg,transparent,var(--gold),transparent)}
.person{position:absolute;top:16px;left:0;right:0;display:flex;justify-content:center;gap:8px;align-items:center}
.person-name{color:var(--gold);font-size:7.5px;font-weight:700}
.person-role{border-left:1px solid #777;padding-left:6px;font-size:5px;line-height:7px}
.card .offices{position:absolute;top:104px;left:0;right:0;text-align:center;font-size:4.6px;line-height:7px}
.offices b,.address b{color:var(--bronze)}
.card .office-label{color:var(--gold);font-weight:700}
.card .web{position:absolute;top:123px;left:0;right:0;text-align:center;font-size:5px;color:var(--gold);font-weight:700}
.disclosure{position:absolute;top:118px;left:10px;right:10px;text-align:center;font-size:3.6px;line-height:5.5px}

/* envelope (top layer) */
.envelope{left:43px;top:313px;width:665px;height:407px;background:var(--paper);box-shadow:0 3px 8px rgba(0,0,0,.35);overflow:hidden;z-index:3;border-radius:14px 14px 0 0}
.envelope .flap{position:absolute;left:0;top:0;width:100%;height:119px;background:var(--card-black)}
.flap-dot{position:absolute;left:322px;top:38px;width:24px;height:24px;border-radius:50%;background:var(--gold)}
.paper-brand{position:absolute;display:flex;align-items:center;gap:8px}
.paper-brand .brand-name{color:var(--ink);font-size:15px}
.paper-brand .brand-dot{width:16px;height:16px}
.paper-tagline{position:absolute;font-size:8.5px;color:var(--ink)}
.envelope .paper-brand{left:31px;top:152px}
.envelope .paper-tagline{left:31px;top:193px}
.watermark{position:absolute;border-radius:50%;background:radial-gradient(circle at 50% 55%,#e2e2e2 0%,var(--mark-tint) 55%,rgba(241,230,218,0) 72%)}
.envelope .watermark{left:480px;top:160px;width:260px;height:260px}
.hairline{position:absolute;height:1px;background:linear-gradient(90deg,transparent,#d3b999 30%,#d3b999 70%,transparent)}
.envelope .hairline{left:80px;right:80px;top:338px}
.address{position:absolute;left:0;right:0;text-align:center;font-size:8px;line-height:10.5px;color:var(--ink)}
.address .web{display:block;margin-top:8px;color:var(--bronze);font-weight:700}
.envelope .address{top:349px}
</style>
</head>
<body>

<section class="sheet letterhead" aria-label="Letterhead">
  <div class="paper-brand"><span class="brand-dot"></span><span class="brand-name">VANTORY WEALTH MANAGEMENT</span></div>
  <p class="paper-tagline">Preferred Wealth Management for Select Individuals</p>
  <div class="hairline top"></div>
  <div class="watermark" aria-hidden="true"></div>
  <div class="hairline bottom"></div>
  <p class="address"><b>Office Address 1 :</b> 1480 W Sagebrush Ln. Tucson, AZ 85741. <b>T</b> (520) 555-0148<br><b>Office Address 2 :</b> 2715 Harbor View Drive, Suite 210. San Diego, CA 92108. <b>T</b> (858) 555-0192<span class="web">www.vantorywm.com</span></p>
</section>

<section class="sheet card card--front" aria-label="Business card front">
  <div class="person">
    <span class="person-name">Daniel Marsh</span>
    <span class="person-role">Chief Executive Officer<br>daniel.marsh@vantorywm.com</span>
  </div>
  <div class="rule" style="top:40px"></div>
  <div class="brand"><span class="brand-dot"></span><span class="brand-name">VANTORY WEALTH MANAGEMENT</span></div>
  <p class="tagline">Preferred Wealth Management for Select Individuals</p>
  <div class="rule" style="top:96px"></div>
  <p class="offices"><span class="office-label">Office Address 1 :</span> 1480 W Sagebrush Ln. Tucson, AZ 85741 <span class="office-label">T</span> (520) 555-0148<br><span class="office-label">Office Address 2 :</span> 2715 Harbor View Drive, Suite 210. San Diego, CA 92108 <span class="office-label">T</span> (858) 555-0192</p>
  <p class="web">www.vantorywm.com</p>
</section>

<section class="sheet card card--back" aria-label="Business card back">
  <div class="brand"><span class="brand-dot"></span><span class="brand-name">VANTORY WEALTH MANAGEMENT</span></div>
  <p class="tagline">Preferred Wealth Management for Select Individuals</p>
  <div class="rule" style="top:96px"></div>
  <p class="disclosure">Investment Advisory Services offered through Harrowfield Asset Partners LLC, a NFR Registered Investment Advisor.<br>Vantory Wealth Management LLC is not affiliated with Harrowfield Asset Partners LLC.</p>
</section>

<section class="sheet envelope" aria-label="Envelope">
  <div class="flap"><span class="flap-dot"></span></div>
  <div class="paper-brand"><span class="brand-dot"></span><span class="brand-name">VANTORY WEALTH MANAGEMENT</span></div>
  <p class="paper-tagline">Preferred Wealth Management for Select Individuals</p>
  <div class="watermark" aria-hidden="true"></div>
  <div class="hairline"></div>
  <p class="address"><b>Office Address 1 :</b> 1480 W Sagebrush Ln. Tucson, AZ 85741. <b>T</b> (520) 555-0148<br><b>Office Address 2 :</b> 2715 Harbor View Drive, Suite 210. San Diego, CA 92108. <b>T</b> (858) 555-0192<span class="web">www.vantorywm.com</span></p>
</section>

</body>
</html>
```